Financial Advisor Resource Firm needs business card design

Need business card design for company in Omaha NE called Meridale Circle. We provide resources to financial advisors....workshop programs, retirement analysis, and insurance planning. I would like to see designs that use grays, greens, black, and white colors. The final design should communicate 'collaboration' and be simple yet attractive to financial planning clients. I will attached our logo and another picture of a puzzle piece coming together. I would like the incorporate the puzzle picture somehow, maybe on the back somehow, with color or just the gray scale....OR, the picture be the front of the card with 'Meridale' definition on it (see upload) and then company logo, employee name, title, address on the back (see ppt uploaded). The following disclosure needs to be included somewhere- Advisory services offered through Stonebrook Assets, LLC.
Updates

I uploaded a svg and ai file of the logo

Target Market(s)

Financial planning clients and financial advisors....so pretty diverse age range of about 40-70.

Industry/Entity Type

Financial Planning

Contact Information for Business Card

Tobias L. Fenwright, MBA
Founder/President
5287 E. Larkin Road
Suite 230
Omaha, NE 68190
Phone- (402) 555-0147
Cell- (402) 555-0183
Fax- (402) 555-0129
email- tobias@meridaleplan.example
web address- www.meridaleplan.example

Colors
1b1b1b
474747
d3d3d3
ffffff
9bcb3c
abd036

Requirements
Must have
• Must include logo provided, must be 2 sided, and must have disclosure...all of these items listed in project description

```html
<!DOCTYPE html>
<html lang="en">
<head>
<meta charset="utf-8">
<title>Meridale Circle – Business Card</title>
<link href="https://fonts.googleapis.com/css2?family=Lato:wght@400;700&family=Roboto+Condensed:wght@400&display=swap" rel="stylesheet">
<style>
  :root {
    --ink: #000000;
    --charcoal: #1b1b1b;
    --gray-dark: #474747;
    --gray-text: #9a9a9a;
    --gray-light: #d3d3d3;
    --white: #ffffff;
    --green: #84c23a;
    --green-text: #9bcb3c;
    --backdrop: #ececec;
  }
  * { box-sizing: border-box; margin: 0; padding: 0; }
  html, body {
    width: 1200px; height: 900px; overflow: hidden;
    background: var(--backdrop);
  }
  .card {
    position: absolute; left: 100px; top: 142px;
    width: 1000px; height: 616px;
    background: var(--ink);
    overflow: hidden;
    font-family: "Lato", sans-serif;
  }
  .accent-band {
    position: absolute; top: 0; right: 0;
    width: 288px; height: 100%;
    background: var(--green);
  }
  .identity { position: absolute; left: 42px; top: 70px; }
  .identity__name {
    font-weight: 700; font-size: 31px; color: var(--green-text);
    letter-spacing: 0.2px; line-height: 1;
  }
  .identity__credential { font-weight: 400; font-size: 27px; }
  .identity__title {
    margin-top: 8px; font-size: 26px; color: var(--gray-text); line-height: 1;
  }
  .address {
    position: absolute; left: 46px; top: 296px;
    font-size: 27px; line-height: 34px; color: var(--gray-text);
  }
  .contacts {
    position: absolute; left: 46px; top: 392px;
    list-style: none;
  }
  .contacts li {
    display: flex; align-items: center; gap: 10px;
    font-size: 27px; line-height: 34.5px; color: var(--gray-text);
  }
  .contacts svg { width: 20px; height: 20px; fill: var(--green-text); flex: none; }
  .emblem {
    position: absolute; left: 456px; top: 56px;
    width: 510px; height: 510px; border-radius: 50%;
    background: radial-gradient(circle at 45% 40%, #ffffff 0%, #f1f1f1 45%, #d9d9d9 100%);
    text-align: center;
  }
  .emblem__name {
    position: absolute; left: 0; right: 0; top: 212px;
    font-family: "Lato", sans-serif; font-weight: 700;
    font-size: 44px; color: var(--charcoal); letter-spacing: 1px;
  }
  .emblem__disclosure {
    position: absolute; left: 0; right: 0; top: 352px;
    font-family: "Roboto Condensed", sans-serif;
    font-size: 20px; line-height: 35px; color: var(--charcoal);
    text-transform: uppercase;
  }
</style>
</head>
<body>
  <div class="card">
    <div class="accent-band"></div>

    <div class="identity">
      <p class="identity__name">TOBIAS L. FENWRIGHT, <span class="identity__credential">MBA</span></p>
      <p class="identity__title">Founder/President</p>
    </div>

    <address class="address" style="font-style:normal">
      5287 E. Larkin Road<br>
      Suite 230 Omaha, NE 68190
    </address>

    <ul class="contacts">
      <li>
        <svg viewBox="0 0 20 20" aria-hidden="true"><path d="M2 7c0-3 4-4 8-4s8 1 8 4v2h-4V7H6v2H2z"/><path d="M5 10h10l2 7H3z"/><circle cx="10" cy="13.5" r="2" fill="#000"/></svg>
        (402) 555-0147
      </li>
      <li>
        <svg viewBox="0 0 20 20" aria-hidden="true"><path d="M6 1h8a1.5 1.5 0 0 1 1.5 1.5v15A1.5 1.5 0 0 1 14 19H6a1.5 1.5 0 0 1-1.5-1.5v-15A1.5 1.5 0 0 1 6 1zm0 2.5v11.5h8V3.5z"/></svg>
        (402) 555-0183
      </li>
      <li>
        <svg viewBox="0 0 20 20" aria-hidden="true"><path d="M5 1h10v5H5z"/><path d="M2 7h16v8h-3v-3H5v3H2z"/><path d="M6 13h8v6H6z"/></svg>
        (402) 555-0129
      </li>
      <li>
        <svg viewBox="0 0 20 20" aria-hidden="true"><path d="M2 4h16v12H2z"/><path d="M2.5 4.5 10 11l7.5-6.5" fill="none" stroke="#000" stroke-width="1.6"/></svg>
        tobias@meridaleplan.example
      </li>
      <li>
        <svg viewBox="0 0 20 20" aria-hidden="true"><circle cx="10" cy="10" r="9"/><path d="M10 1v18M1 10h18M4 4.5c3.5 2 8.5 2 12 0M4 15.5c3.5-2 8.5-2 12 0" fill="none" stroke="#000" stroke-width="1.2"/></svg>
        www.meridaleplan.example
      </li>
    </ul>

    <div class="emblem">
      <p class="emblem__name">MERIDALE CIRCLE</p>
      <p class="emblem__disclosure">Advisory services offered through<br>Stonebrook Assets, LLC.</p>
    </div>
  </div>
</body>
</html>
```